American cannabis tech company business card design

Pavrel.com is seeking a modern, professional, and brand-aligned business card that represents our company and its core values: Mission, Story, Values, and Impact. As an innovative cannabis company, we want a business card that is not only visually appealing but also serves as a representation of who we are and what we stand for.

Project Scope: Design a double-sided business card that integrates our brand identity and core values. Incorporate our key brand elements, ensuring a sleek and contemporary aesthetic. Visually reflect our core values (Mission, Story, Values, Impact) in a way that is engaging yet professional.

Target Market(s)

Vendors, third parties,

Contact Information for Business Card

Contact details (name, title, email, phone, website, etc.)

Font styles to use
Other font styles liked:
• Caslon, Centra

Colors

Designer to choose colors to be used in the design.

Requirements
Must have
• Pavrel.com logo and branding A creative yet clean way to integrate our core values (Mission, Story, Values, Impact) Modern typography and a well-structured layout
Nice to have
• forest green, grey, white, black
Should not have
• references to marijuana, leafs, plants, or related product

```html
<!DOCTYPE html>
<html lang="en">
<head>
<meta charset="utf-8">
<title>Pavrel.com Business Card</title>
<link href="https://fonts.googleapis.com/css2?family=Poppins:wght@400;500;600;700&display=swap" rel="stylesheet">
<style>
  :root {
    --ink: #1b201c;
    --page: #e7e4df;
    --card-top: #f5f4f1;
    --card-bottom: #e2e4e7;
    --name: #d9d2c4;
    --title: #c9c2b5;
    --motto: #b8b0a2;
    --icon: #ece8e0;
  }
  * { margin: 0; padding: 0; box-sizing: border-box; }
  html, body {
    width: 1200px; height: 970px; overflow: hidden;
    background: var(--page);
    font-family: "Poppins", sans-serif;
  }
  .card {
    position: absolute; left: 50px; top: 172px;
    width: 1100px; height: 626px;
    background: linear-gradient(160deg, var(--card-top), var(--card-bottom));
    overflow: hidden;
    box-shadow: 0 10px 30px rgba(0,0,0,0.12);
  }
  .wordmark {
    position: absolute; left: 61px; top: 108px;
    font-size: 84px; font-weight: 700; line-height: 1;
    color: var(--ink); letter-spacing: -1px;
  }
  .name-pill {
    position: absolute; left: 634px; top: 84px;
    width: 466px; height: 115px;
    background: var(--ink);
    border-radius: 58px 0 0 58px;
    padding: 22px 0 0 84px;
  }
  .name-pill .person {
    font-size: 33px; font-weight: 600; color: var(--name);
    line-height: 1.1; letter-spacing: 0.5px;
  }
  .name-pill .role {
    font-size: 23px; font-weight: 400; color: var(--title); line-height: 1.2;
  }
  .contact-rail {
    position: absolute; left: 0; top: 415px;
    width: 1100px; height: 6px; background: var(--ink);
  }
  .contact-icon {
    position: absolute; top: 384px;
    width: 68px; height: 68px; border-radius: 50%;
    background: var(--ink);
    display: flex; align-items: center; justify-content: center;
  }
  .contact-text {
    position: absolute; top: 487px;
    font-size: 28px; font-weight: 400; color: var(--ink);
    transform: translateX(-50%); white-space: nowrap;
  }
  .values-band {
    position: absolute; left: 0; top: 536px;
    width: 1100px; height: 90px; background: var(--ink);
    display: flex; align-items: center; justify-content: center;
  }
  .values-band p {
    font-size: 26px; font-weight: 400; color: var(--motto);
    letter-spacing: 5px;
  }
</style>
</head>
<body>
  <div class="card">
    <div class="wordmark">PAVREL</div>

    <div class="name-pill">
      <div class="person">LENA R. CARVER</div>
      <div class="role">Director</div>
    </div>

    <div class="contact-rail"></div>

    <div class="contact-icon" style="left:160px">
      <svg width="34" height="30" viewBox="0 0 34 30" aria-hidden="true">
        <path d="M2 9c0-4 6-6 15-6s15 2 15 6v3h-7V9c-3-1-13-1-16 0v3H2z" fill="var(--icon)"/>
        <path d="M8 13h18l4 14H4z" fill="var(--icon)"/>
        <circle cx="17" cy="20" r="4" fill="var(--ink)"/>
      </svg>
    </div>
    <div class="contact-icon" style="left:513px">
      <svg width="34" height="24" viewBox="0 0 34 24" aria-hidden="true">
        <rect x="1" y="1" width="32" height="22" fill="none" stroke="var(--icon)" stroke-width="2.5"/>
        <path d="M1 1l16 12L33 1M1 23l12-11M33 23L21 12" fill="none" stroke="var(--icon)" stroke-width="2.5"/>
      </svg>
    </div>
    <div class="contact-icon" style="left:867px">
      <svg width="34" height="34" viewBox="0 0 34 34" aria-hidden="true">
        <g fill="none" stroke="var(--icon)" stroke-width="2">
          <circle cx="17" cy="17" r="15"/>
          <ellipse cx="17" cy="17" rx="7" ry="15"/>
          <path d="M17 2v30M2 17h30M5 9h24M5 25h24"/>
        </g>
      </svg>
    </div>

    <div class="contact-text" style="left:194px">+1 555-014-2298</div>
    <div class="contact-text" style="left:547px">team@pavrel.com</div>
    <div class="contact-text" style="left:901px">www.PAVREL.com</div>

    <div class="values-band">
      <p>Mission | Story | Values and Impact</p>
    </div>
  </div>
</body>
</html>
```